Computer consultant business card

Bexil Software is a newly started computer consulting company. It's a small one-man company that provides mostly Vornix applications but also websites in collaboration with designers. I'm running this company on the side of full time university studies.

I want the final design to be clean and memorable. Be creative! :)

Some inspiration:
http://www.pixelmarta.com/design/48317
http://www.pixelmarta.com/design/2739164/business-card-design-by-frostlynk
http://www.pixelmarta.com/design/604281/business-card-design-by-koralind-vestrabanu

See attachment for my company logo.
Updates

I would like to thank everyone for submitting! I'll need a couple of days to review and ultimately select a design.

Target Market(s)

Non-technical entrepreneurs and small companies.

Industry/Entity Type

University

Requirements
Must have
• My company logo.
In any way, both colors from my logo.
First- and last name, e-mail and phone number.
Double-sided design.
Nice to have
• Something creative with the symbol in my logo

```html
<!DOCTYPE html>
<html lang="en">
<head>
<meta charset="utf-8">
<title>Bexil Software – Business Card</title>
<link rel="stylesheet" href="https://fonts.googleapis.com/css2?family=Jost:wght@400;500;600&display=swap">
<style>
  :root {
    --brand-blue: #1f7bfa;
    --brand-dark: #353535;
    --card-white: #ffffff;
    --text-grey: #4a4a4a;
    --backdrop: #eceae6;
    --card-shadow: rgba(0, 0, 0, 0.18);
  }
  * { box-sizing: border-box; margin: 0; padding: 0; }
  html, body {
    width: 1200px;
    height: 823px;
    overflow: hidden;
    background: var(--backdrop);
    font-family: "Jost", sans-serif;
  }
  .canvas {
    position: relative;
    width: 1200px;
    height: 823px;
  }
  .card {
    position: absolute;
    width: 520px;
    height: 300px;
    border-radius: 22px;
    overflow: hidden;
    box-shadow: 0 10px 28px var(--card-shadow);
  }
  .card-front {
    left: 60px;
    top: 190px;
    background: var(--card-white);
  }
  .card-back {
    left: 620px;
    top: 330px;
    background: var(--brand-blue);
    display: flex;
    align-items: center;
    justify-content: center;
    gap: 22px;
  }
  .wave {
    position: absolute;
    inset: 0;
    width: 100%;
    height: 100%;
  }
  .brand {
    position: absolute;
    left: 46px;
    top: 48px;
    display: flex;
    align-items: center;
    gap: 20px;
  }
  .brand-dot {
    width: 58px;
    height: 58px;
    border-radius: 50%;
    background: var(--brand-blue);
  }
  .brand-name {
    font-size: 78px;
    font-weight: 500;
    line-height: 1;
    color: var(--brand-dark);
    letter-spacing: 1px;
  }
  .address {
    position: absolute;
    left: 0;
    right: 0;
    top: 160px;
    text-align: center;
    font-size: 15px;
    letter-spacing: 1.2px;
    color: var(--text-grey);
  }
  .contact {
    position: absolute;
    right: 26px;
    top: 196px;
    list-style: none;
    color: var(--card-white);
    font-size: 14px;
    line-height: 22px;
  }
  .contact li {
    display: flex;
    align-items: center;
    justify-content: flex-end;
    gap: 7px;
  }
  .contact svg { width: 12px; height: 12px; fill: var(--card-white); }
  .person {
    position: absolute;
    left: 26px;
    bottom: 22px;
    color: var(--card-white);
    font-size: 15px;
  }
  .person .first {
    font-size: 21px;
    font-weight: 600;
  }
  .back-dot {
    width: 80px;
    height: 80px;
    border-radius: 50%;
    background: var(--card-white);
  }
  .back-name {
    font-size: 96px;
    font-weight: 500;
    line-height: 1;
    color: var(--card-white);
  }
</style>
</head>
<body>
<main class="canvas">
  <section class="card card-front" aria-label="Business card front">
    <svg class="wave" viewBox="0 0 520 300" preserveAspectRatio="none" aria-hidden="true">
      <path d="M0,232 C130,292 310,250 520,150 L520,300 L0,300 Z" fill="var(--brand-blue)"/>
      <path d="M0,222 C130,280 310,238 520,138" fill="none" stroke="var(--brand-dark)" stroke-width="5"/>
      <path d="M0,213 C130,270 310,228 520,128" fill="none" stroke="var(--brand-blue)" stroke-width="1.5"/>
    </svg>
    <div class="brand">
      <span class="brand-dot"></span>
      <span class="brand-name">bexil</span>
    </div>
    <p class="address">00, Complex name, City, State 0042</p>
    <ul class="contact">
      <li>
        <svg viewBox="0 0 24 24" aria-hidden="true"><path d="M6.6 10.8a15 15 0 0 0 6.6 6.6l2.2-2.2c.3-.3.7-.4 1-.2 1.1.4 2.3.6 3.6.6.6 0 1 .4 1 1V20c0 .6-.4 1-1 1A17 17 0 0 1 3 4c0-.6.4-1 1-1h3.5c.6 0 1 .4 1 1 0 1.3.2 2.5.6 3.6.1.3 0 .7-.2 1z"/></svg>
        0612 748390
      </li>
      <li>
        <svg viewBox="0 0 24 24" aria-hidden="true"><path d="M2 5h20v14H2z M2 5l10 8 10-8" fill="var(--card-white)" stroke="var(--brand-blue)" stroke-width="1.5"/></svg>
        info@bexil.com
      </li>
    </ul>
    <p class="person"><span class="first">First Name,</span> Last Name</p>
  </section>

  <section class="card card-back" aria-label="Business card back">
    <span class="back-dot"></span>
    <span class="back-name">bexil</span>
  </section>
</main>
</body>
</html>
```